Stationery for Villa Marenta Design Hotel**

Who we are:

Wander on an isolated beach while breathing in the fresh, salty, sea air. Listen to the warm Pacific wind rustling through green palm trees as you walk to a pristine lagoon. Feel the delicious warmth of the sun kiss your skin; the beach is yours. At Villa Marenta you can experience a vacation in undisturbed, natural beauty. We have created a place for you to find new strength, relaxation, and inner harmony. We offer total rest to the experienced traveler from all over the world.

We are a brand new and smartly built design-hotel (under construction) close to a unique beach and a fantastic surf spot in Huatulco, Southwest Mexico.

As you can see in the attachments, we do have an established corporate design, but as for now still need a format for booklets for information around our hotel and things to do in the area, important numbers (we fill in the content for that one).

Our corporate colors:
green #64b445, brown #b07043, blue #0ab7cf, yellow # f9b02a and #fcc01a, navy #444f69
Corporate fonts:
Krub and Miller Banner.
For further information access:
www.villamarenta.example
https://slidevault.example/view/QmPxLwZrTyKsNbVcHdJe/

Social Media: VillaMarenta

Industry/Entity Type

Hotel

Font styles to use
Other font styles liked:
• Krub, Miller Banner

Requirements
Must have
• Stick to Logo Design, defined corporate elements, logo, colors, fonts and general touch and feel
Nice to have
• Who we are:

Our corporate colors:
Corporate fonts:
Krub and Miller Banner.
www.villamarenta.example

Social Media: VillaMarenta

```html
<!DOCTYPE html>
<html lang="en">
<head>
<meta charset="utf-8">
<title>Villa Marenta Design Hotel – Business Cards</title>
<link rel="stylesheet" href="https://fonts.googleapis.com/css2?family=Krub:wght@400;600;700&family=Libre+Baskerville&display=swap">
<style>
  :root {
    --stage: #d6d8db;
    --card-dark: #2a2a2b;
    --card-light: #ffffff;
    --gold: #d9a520;
    --orange: #f9b02a;
    --green: #64b445;
    --teal: #0ab7cf;
    --ink: #555a60;
    --name: #f0a81c;
    --brown: #3a2a1a;
  }
  * { box-sizing: border-box; margin: 0; padding: 0; }
  html, body { width: 1200px; height: 900px; overflow: hidden; }
  body {
    background: var(--stage);
    font-family: "Krub", sans-serif;
    position: relative;
  }
  .card {
    position: absolute;
    left: 300px;
    width: 600px;
    height: 340px;
    border-radius: 22px;
    overflow: hidden;
    background: var(--card-dark);
    box-shadow: 0 10px 28px rgba(0,0,0,.25);
  }
  .card--contact { top: 60px; }
  .card--brand { top: 480px; }

  .tick {
    position: absolute;
    width: 6px; height: 26px;
    background: var(--teal);
  }

  /* Contact side */
  .contact-panel {
    position: absolute; left: 0; top: 0;
    width: 290px; height: 100%;
    background: var(--card-light);
  }
  .contact-bands { position: absolute; left: 0; top: 0; }
  .person { position: absolute; left: 48px; top: 30px; }
  .person__name {
    font-weight: 700; font-size: 27px; color: var(--name); line-height: 1.1;
  }
  .person__role {
    font-size: 17px; color: #8a8f94; margin-top: 2px;
    padding-bottom: 6px; border-bottom: 2px solid var(--teal); width: 92px;
  }
  .contact-list { position: absolute; left: 28px; top: 118px; list-style: none; }
  .contact-list li {
    display: flex; align-items: center; gap: 10px;
    font-family: "Libre Baskerville", serif; font-size: 14px; color: var(--ink);
    height: 25px;
  }
  .icon {
    width: 16px; height: 16px; border-radius: 3px; background: var(--orange);
    display: flex; align-items: center; justify-content: center; flex: none;
  }
  .address {
    position: absolute; left: 66px; top: 222px;
    font-family: "Libre Baskerville", serif; font-size: 14.5px; color: var(--brown);
    line-height: 1.45;
  }
  .pin { position: absolute; left: 20px; top: 218px; }

  .brand-lockup {
    position: absolute; display: flex; align-items: center; gap: 12px;
  }
  .brand-lockup__mark {
    width: 26px; height: 26px; border: 2px solid var(--gold);
  }
  .brand-lockup__name {
    font-weight: 600; font-size: 30px; color: var(--gold); letter-spacing: 1px;
  }
  .card--contact .brand-lockup { left: 330px; top: 150px; }

  /* Brand side */
  .brand-band { position: absolute; left: 0; bottom: 0; }
  .card--brand .brand-lockup { left: 215px; top: 80px; }
  .website {
    position: absolute; left: 230px; top: 275px;
    font-family: "Libre Baskerville", serif; font-size: 18px; color: #222;
  }
</style>
</head>
<body>

  <section class="card card--contact" aria-label="Business card, contact side">
    <div class="contact-panel"></div>
    <svg class="contact-bands" width="600" height="340" viewBox="0 0 600 340">
      <polygon points="0,196 290,196 290,340 0,340" fill="#f9b02a"/>
      <polygon points="150,340 290,250 290,340" fill="#64b445"/>
    </svg>
    <div class="person">
      <p class="person__name">Example Name</p>
      <p class="person__role">Designation</p>
    </div>
    <ul class="contact-list">
      <li><span class="icon"><svg width="10" height="10" viewBox="0 0 10 10"><path d="M2 1 L4 1 L4.6 3 L3.4 3.8 Q4.3 5.8 6.2 6.6 L7 5.4 L9 6 L9 8 Q4 9 1 2 Z" fill="#fff"/></svg></span>+52 (555) 010 4471</li>
      <li><span class="icon"><svg width="10" height="8" viewBox="0 0 10 8"><rect x=".5" y=".5" width="9" height="7" fill="none" stroke="#fff"/><path d="M.5 .5 L5 4.5 L9.5 .5" fill="none" stroke="#fff"/></svg></span>hello@villamarenta.example</li>
      <li><span class="icon"><svg width="10" height="10" viewBox="0 0 10 10"><circle cx="5" cy="5" r="4" fill="none" stroke="#fff"/><path d="M1 5 H9 M5 1 V9" stroke="#fff"/></svg></span>www.villamarenta.example</li>
    </ul>
    <svg class="pin" width="26" height="26" viewBox="0 0 26 26">
      <rect width="26" height="26" rx="5" fill="#3a2a1a"/>
      <path d="M13 5 a5 5 0 0 1 5 5 c0 4 -5 10 -5 10 s-5 -6 -5 -10 a5 5 0 0 1 5 -5z" fill="#fff"/>
      <circle cx="13" cy="10" r="2" fill="#3a2a1a"/>
    </svg>
    <p class="address">Villa Marenta, Playa Serena,<br>Costa Azul, Mexiko</p>
    <div class="brand-lockup">
      <span class="brand-lockup__mark"></span>
      <span class="brand-lockup__name">Villa Marenta</span>
    </div>
    <span class="tick" style="right:0; top:24px;"></span>
    <span class="tick" style="right:0; bottom:24px;"></span>
  </section>

  <section class="card card--brand" aria-label="Business card, brand side">
    <svg class="brand-band" width="600" height="110" viewBox="0 0 600 110">
      <rect x="0" y="0" width="600" height="110" fill="#ffffff"/>
      <rect x="0" y="0" width="190" height="110" fill="#f9b02a"/>
      <polygon points="60,110 190,30 190,110" fill="#64b445"/>
    </svg>
    <div class="brand-lockup">
      <span class="brand-lockup__mark"></span>
      <span class="brand-lockup__name">Villa Marenta</span>
    </div>
    <p class="website">www.villamarenta.example</p>
    <span class="tick" style="left:0; top:24px;"></span>
    <span class="tick" style="right:0; top:24px;"></span>
  </section>

</body>
</html>
```